Road Construction Company needs business cards

We would like a new business card designed for our business.

We're a road construction company based in Qld, Australia.

Can the business card please have the following information on it.

Name: Warren Halbeck
Position: General Manager
Phone: 0472 915 348
Email: Warren.halbeck@tovrin.com.au
Address: 87 Marrow Ave, Pendlebay, QLD, 4023
Website: www.tovrin.com.au

Visually we'd like the card to be professional and simple.

Attached is our logo.

Our website is www.tovrin.com.au

Target Market(s)

Men aged 25-60

Contact Information for Business Card

As listed in project description

Font styles to use
Serif

Requirements
Must have
• Large logo on back of card

```html
<!DOCTYPE html>
<html lang="en">
<head>
<meta charset="utf-8">
<title>Tovrin Business Card</title>
<link rel="stylesheet" href="https://fonts.googleapis.com/css2?family=Open+Sans:wght@400;600;700&display=swap">
<style>
  :root {
    --page: #2a2a2e;
    --royal: #1457a8;
    --sky: #45abdf;
    --charcoal: #1f1f23;
    --white: #ffffff;
    --card-w: 540px;
    --card-h: 310px;
  }
  * { box-sizing: border-box; margin: 0; padding: 0; }
  html, body {
    width: 1200px;
    height: 780px;
    overflow: hidden;
    background: var(--page);
    font-family: "Open Sans", Arial, sans-serif;
  }
  .sheet {
    width: 1200px;
    height: 780px;
    display: flex;
    align-items: center;
    justify-content: center;
    gap: 50px;
  }
  .card {
    position: relative;
    width: var(--card-w);
    height: var(--card-h);
    border-radius: 22px;
    overflow: hidden;
    box-shadow: 0 0 0 3px var(--sky), 0 18px 40px rgba(0,0,0,.45);
  }

  /* Front */
  .card-front {
    background: var(--royal);
    display: flex;
    align-items: center;
    justify-content: center;
  }
  .brand-name {
    font-weight: 700;
    color: var(--white);
    letter-spacing: 4px;
    line-height: 1;
  }
  .card-front .brand-name { font-size: 96px; }

  /* Back */
  .card-back { background: var(--charcoal); }
  .back-swoosh {
    position: absolute;
    inset: 0;
    width: 100%;
    height: 100%;
  }
  .name-tab {
    position: absolute;
    top: 0;
    right: 22px;
    width: 16px;
    height: 68px;
    background: var(--royal);
  }
  .person {
    position: absolute;
    top: 18px;
    right: 50px;
    text-align: right;
  }
  .person-name {
    font-size: 30px;
    font-weight: 700;
    color: var(--royal);
    line-height: 1.1;
  }
  .person-role {
    font-size: 14px;
    font-weight: 600;
    color: var(--white);
    margin-top: 2px;
  }
  .card-back .brand-name {
    position: absolute;
    top: 112px;
    left: 34px;
    font-size: 50px;
    color: var(--royal);
  }
  .address {
    position: absolute;
    left: 80px;
    top: 180px;
    font-size: 13.5px;
    color: var(--white);
    line-height: 1.35;
  }
  .contacts {
    position: absolute;
    left: 50px;
    top: 226px;
    list-style: none;
  }
  .contacts li {
    display: flex;
    align-items: center;
    gap: 10px;
    font-size: 13.5px;
    color: var(--white);
    line-height: 1.4;
    height: 20px;
  }
  .contacts svg { width: 14px; height: 14px; flex: none; }
</style>
</head>
<body>
<main class="sheet">
  <section class="card card-front" aria-label="Card front">
    <span class="brand-name">TOVRIN</span>
  </section>

  <section class="card card-back" aria-label="Card back">
    <svg class="back-swoosh" viewBox="0 0 540 310" preserveAspectRatio="none" aria-hidden="true">
      <path d="M540 90 C 500 200, 400 290, 250 310 L 540 310 Z" fill="#1457a8"/>
      <path d="M470 200 C 420 265, 330 295, 220 300 L 225 306 C 345 302, 440 268, 475 205 Z" fill="#45abdf"/>
    </svg>

    <div class="name-tab"></div>
    <div class="person">
      <p class="person-name">Warren Halbeck</p>
      <p class="person-role">General Manager</p>
    </div>

    <span class="brand-name">TOVRIN</span>

    <p class="address">87 Marrow Ave,<br>Pendlebay, QLD, 4023</p>

    <ul class="contacts">
      <li>
        <svg viewBox="0 0 16 16" aria-hidden="true"><circle cx="8" cy="8" r="8" fill="#45abdf"/><path d="M5 4.5l1.6-.4.9 2-1 .8a5 5 0 0 0 2.6 2.6l.8-1 2 .9-.4 1.6c-3.6.3-6.8-2.9-6.5-6.5z" fill="#1f1f23"/></svg>
        0472 915 348
      </li>
      <li>
        <svg viewBox="0 0 16 16" aria-hidden="true"><circle cx="8" cy="8" r="8" fill="#45abdf"/><circle cx="8" cy="8" r="4.5" fill="none" stroke="#1f1f23" stroke-width="1.2"/><path d="M3.5 8h9M8 3.5c-2 2.5-2 6.5 0 9M8 3.5c2 2.5 2 6.5 0 9" fill="none" stroke="#1f1f23" stroke-width="1"/></svg>
        www.tovrin.com.au
      </li>
      <li>
        <svg viewBox="0 0 16 16" aria-hidden="true"><circle cx="8" cy="8" r="8" fill="#45abdf"/><rect x="4" y="5" width="8" height="6" fill="none" stroke="#1f1f23" stroke-width="1.2"/><path d="M4 5l4 3.3L12 5" fill="none" stroke="#1f1f23" stroke-width="1.2"/></svg>
        Warren.halbeck@tovrin.com.au
      </li>
    </ul>
  </section>
</main>
</body>
</html>
```